Veltrane Group Business Card Design

The CEO is looking for a new trendy look for his business card.
You can stay with current branding or come up with something new/creative. It can be 3D, including Medical Office buildings. You can use our logo in a variety of colors. Please include name, title, company name, company website, email address, cell number

Target Market(s)

Real Estate Development and Construction

Industry/Entity Type

Health care real estate

Contact Information for Business Card

Rohesh Kamdar, CEO M-604.781.2249 E-roheshkamdar@veltrane.com Address:4180 Lindqvist Ave, Tampa, FL 33482 www.veltrane.com

Font styles to use
Other font styles liked:
• Be creative

Requirements
Must have
• Creative, trendy look
Nice to have
• Please go to our website to get a feel- www. veltrane.com
Should not have
• small fonts

```html
<!DOCTYPE html>
<html lang="en">
<head>
<meta charset="UTF-8">
<title>Veltrane Group — Business Card</title>
<link href="https://fonts.googleapis.com/css2?family=Open+Sans:wght@400;700&display=swap" rel="stylesheet">
<style>
  :root {
    --backdrop: #2b2e32;
    --card: #ffffff;
    --ink: #111111;
    --bar: #0d0d0d;
    --rule: #333333;
  }
  * { margin: 0; padding: 0; box-sizing: border-box; }
  html, body { width: 1200px; height: 900px; overflow: hidden; }
  body {
    background: var(--backdrop);
    font-family: "Open Sans", Arial, sans-serif;
    color: var(--ink);
    position: relative;
  }
  .card {
    position: absolute;
    left: 250px;
    width: 700px;
    height: 400px;
    background: var(--card);
    overflow: hidden;
  }
  .card--front { top: 35px; }
  .card--contact { top: 465px; }

  .corner-bar { position: absolute; background: var(--bar); }
  .corner-bar--top { left: 0; top: 0; width: 230px; height: 16px; }
  .corner-bar--bottom { right: 0; bottom: 0; width: 300px; height: 34px; }

  .brand {
    position: absolute;
    display: flex;
    align-items: center;
    font-weight: 700;
    color: var(--ink);
    white-space: nowrap;
    line-height: 1;
  }
  .brand__mark { display: block; background: var(--ink); flex: none; }

  .card--front .brand {
    left: 50%;
    top: 50%;
    transform: translate(-50%, -50%);
    font-size: 58px;
    gap: 18px;
  }
  .card--front .brand__mark { width: 40px; height: 40px; }

  .card--contact .brand {
    left: 40px;
    top: 100px;
    font-size: 29px;
    gap: 12px;
  }
  .card--contact .brand__mark { width: 22px; height: 22px; }

  .divider {
    position: absolute;
    left: 360px;
    top: 78px;
    width: 1px;
    height: 230px;
    background: var(--rule);
  }
  .contact {
    position: absolute;
    left: 384px;
    top: 80px;
  }
  .contact__name { font-size: 26px; font-weight: 700; line-height: 1.15; }
  .contact__title { font-size: 15px; margin-bottom: 10px; }
  .contact__address { font-size: 15px; line-height: 1.35; margin-bottom: 8px; }
  .contact__list { list-style: none; font-size: 15px; line-height: 1.6; }
  .contact__list li { display: flex; align-items: center; gap: 8px; }
  .contact__list svg { width: 13px; height: 13px; fill: var(--ink); flex: none; }
</style>
</head>
<body>

<section class="card card--front" aria-label="Card front">
  <span class="corner-bar corner-bar--top"></span>
  <span class="corner-bar corner-bar--bottom"></span>
  <p class="brand"><span class="brand__mark"></span>Veltrane Group</p>
</section>

<section class="card card--contact" aria-label="Card back">
  <span class="corner-bar corner-bar--top"></span>
  <span class="corner-bar corner-bar--bottom"></span>
  <p class="brand"><span class="brand__mark"></span>Veltrane Group</p>
  <span class="divider"></span>
  <div class="contact">
    <p class="contact__name">Rohesh Kamdar</p>
    <p class="contact__title">CEO</p>
    <p class="contact__address">4180 Lindqvist Ave,<br>Tampa, FL 33482</p>
    <ul class="contact__list">
      <li>
        <svg viewBox="0 0 24 24" aria-hidden="true"><path d="M6.6 10.8a15 15 0 0 0 6.6 6.6l2.2-2.2a1 1 0 0 1 1-.25 11.4 11.4 0 0 0 3.6.57 1 1 0 0 1 1 1V20a1 1 0 0 1-1 1A17 17 0 0 1 3 4a1 1 0 0 1 1-1h3.5a1 1 0 0 1 1 1c0 1.25.2 2.45.57 3.57a1 1 0 0 1-.25 1z"/></svg>
        604.781.2249
      </li>
      <li>
        <svg viewBox="0 0 24 24" aria-hidden="true"><path d="M2 5h20v14H2z M2 5l10 8 10-8" /></svg>
        roheshkamdar@veltrane.com
      </li>
      <li>
        <svg viewBox="0 0 24 24" aria-hidden="true"><path d="M12 2a10 10 0 1 0 0 20 10 10 0 0 0 0-20zm0 2c.9 0 2.2 2 2.7 5H9.3C9.8 6 11.1 4 12 4zM4.3 11h3a18 18 0 0 0 0 2h-3a8 8 0 0 1 0-2zm5 0h5.4a16 16 0 0 1 0 2H9.3a16 16 0 0 1 0-2zm7.4 0h3a8 8 0 0 1 0 2h-3a18 18 0 0 0 0-2zM9.3 15h5.4c-.5 3-1.8 5-2.7 5s-2.2-2-2.7-5z"/></svg>
        www.veltrane.com
      </li>
    </ul>
  </div>
</section>

</body>
</html>
```